Tidewell Homecare

I am looking to have a website designed for a housekeeping company that looks similar to this one. https://marloweshomecare.example/

I need 5 websites designed but will start with this one to see how I like it.

Industry/Entity Type

House Cleaning

Coding

Coded - Design and coding required

Number of Pages Required

5+ page

Font styles to use
Serif
Script

Colors
ffffff
fdf9cf
fbf289
fbee3f
d6edf3
86cae7
33a6d7
edf1f8
cedeed

```html
<!DOCTYPE html>
<html lang="en">
<head>
<meta charset="utf-8">
<title>Tidewell Homecare</title>
<link href="https://fonts.googleapis.com/css2?family=Roboto:wght@400;500;700&display=swap" rel="stylesheet">
<style>
:root{
  --white:#ffffff;
  --blue:#33a6d7;
  --blue-soft:#86cae7;
  --blue-pale:#d6edf3;
  --yellow:#fbee3f;
  --ink:#222222;
  --text:#333333;
  --line:#cedeed;
  --footer:#2d2f31;
}
*{box-sizing:border-box;margin:0;padding:0}
html,body{width:1200px;height:4003px;overflow:hidden}
body{font-family:'Roboto',sans-serif;color:var(--text);background:var(--white);position:relative}
.abs{position:absolute}
.center{text-align:center}

/* header */
.site-header{position:absolute;top:0;left:0;width:1200px;height:93px;background:var(--white)}
.brand{position:absolute;left:110px;top:28px;display:flex;align-items:center;gap:12px}
.brand-mark{width:38px;height:38px;border-radius:50%;background:var(--blue)}
.brand-name{font-size:22px;font-weight:500;color:var(--blue);line-height:1.2}
.main-nav{position:absolute;left:485px;top:36px;display:flex;gap:34px;font-size:16px;color:var(--ink)}
.main-nav .active{color:var(--blue)}

/* hero */
.hero{position:absolute;top:93px;left:0;width:1200px;height:521px;background:linear-gradient(120deg,#e8ebee 0%,#d5dade 45%,#bfc6cc 100%)}
.hero-title{position:absolute;top:235px;width:1200px;text-align:center;font-size:34px;font-weight:700;color:var(--white);text-shadow:0 2px 6px rgba(0,0,0,.45)}
.hero-dots{position:absolute;left:1082px;top:232px;display:flex;flex-direction:column;gap:8px}
.hero-dots span{width:10px;height:10px;border-radius:50%;background:var(--white)}
.hero-dots span.on{background:var(--blue)}

/* service boxes */
.service{position:absolute;top:614px;height:249px;text-align:center;padding:0 28px}
.service h3{margin-top:56px;font-size:26px;font-weight:500;color:var(--white)}
.service p{margin-top:18px;font-size:16px;line-height:29px;color:var(--white)}
.service.yellow h3,.service.yellow p{color:var(--ink)}
.service-icon{position:absolute;top:-54px;left:50%;margin-left:-50px;width:100px;height:100px;border-radius:50%;display:flex;align-items:center;justify-content:center}
.blue{background:var(--blue)}
.yellow{background:var(--yellow)}

/* welcome */
.section-title{font-size:33px;font-weight:500;color:var(--ink);text-align:center;width:1200px;position:absolute;left:0}
.welcome-text{position:absolute;left:180px;width:840px;top:1024px;text-align:center;font-size:16px;line-height:32px}
.btn{position:absolute;display:flex;align-items:center;justify-content:center;border-radius:24px;font-size:16px;font-weight:500}
.btn-blue{background:var(--blue);color:var(--white)}
.btn-white{background:var(--white);color:var(--blue)}

/* cleaning services band */
.clean-band{position:absolute;top:1299px;left:0;width:1200px;height:511px;background:var(--blue)}
.clean-photo{position:absolute;left:0;top:0}
.clean-band h2{position:absolute;left:620px;top:50px;font-size:34px;font-weight:500;color:var(--white)}
.clean-sub{position:absolute;left:620px;top:112px;font-size:16px;font-weight:700;color:var(--white)}
.tick-item{position:absolute;left:618px;display:flex;gap:18px;font-size:17px;line-height:32px;color:var(--white);width:500px}
.tick-item svg{flex:none;margin-top:4px}

/* why choose */
.why-sub{position:absolute;left:250px;width:700px;top:1966px;text-align:center;font-size:16px;line-height:32px;color:var(--ink)}
.feature{position:absolute;width:300px}
.feature h4{font-size:18px;font-weight:700;color:#444;margin-bottom:8px}
.feature p{font-size:15px;line-height:30px;color:#444}
.feature.left{text-align:right}
.f-icon{position:absolute;width:62px;height:62px;border-radius:50%;background:var(--blue-pale);display:flex;align-items:center;justify-content:center}
.f-icon span{width:48px;height:48px;border-radius:50%;background:var(--blue);display:flex;align-items:center;justify-content:center}

/* estimate */
.estimate{position:absolute;top:2455px;left:0;width:1200px;height:435px;background:linear-gradient(90deg,rgba(51,166,215,.95),rgba(70,176,222,.92))}
.estimate h2{position:absolute;top:76px;width:1200px;text-align:center;font-size:34px;font-weight:500;color:var(--white)}
.field{position:absolute;width:233px;height:52px;background:var(--white);display:flex;align-items:center;justify-content:space-between;padding:0 26px;font-size:15px;color:#444}
.field em{color:#e53935;font-style:normal}

/* blog */
.blog-card{position:absolute;top:3075px;width:306px;height:367px;border:1px solid #e2e2e2;background:var(--white);text-align:center}
.blog-img{width:304px;height:183px;background:linear-gradient(135deg,#dfe4e8,#b9c7d0)}
.date{position:absolute;right:14px;top:14px;width:34px;height:110px;border-radius:17px;background:var(--blue);color:var(--white);font-size:17px;padding-top:8px}
.date small{display:block;font-size:10px;line-height:13px;margin-top:8px}
.author{margin-top:26px;display:flex;justify-content:center;align-items:center;gap:10px;font-size:16px;font-weight:500;color:var(--ink)}
.author i{width:28px;height:28px;border-radius:50%;background:var(--blue);display:block}
.blog-card p{margin-top:14px;padding:0 30px;font-size:15px;line-height:26px;color:#444}
.blog-card .btn{left:84px;width:138px;height:40px;bottom:-20px;font-size:15px}
.pager{position:absolute;top:3530px;left:576px;display:flex;gap:8px}
.pager span{width:9px;height:9px;border-radius:50%;background:var(--blue)}
.pager span.on{background:var(--ink)}

/* footer */
.site-footer{position:absolute;top:3621px;left:0;width:1200px;height:382px;background:var(--footer);color:var(--white)}
.site-footer h5{position:absolute;top:68px;font-size:19px;font-weight:700}
.f-about{position:absolute;left:113px;top:112px;width:310px;font-size:15px;line-height:26px}
.f-links{position:absolute;left:463px;top:118px;font-size:15px;line-height:30px;list-style:none}
.f-contact{position:absolute;left:643px;top:120px;font-size:18px;line-height:26px}
.socials{position:absolute;left:948px;top:110px;display:flex;gap:20px}
.socials span{width:38px;height:38px;border-radius:50%;border:2px solid var(--white)}
.copyright{position:absolute;top:334px;width:1200px;text-align:center;font-size:13px}
</style>
</head>
<body>

<header class="site-header">
  <div class="brand"><span class="brand-mark"></span><span class="brand-name">Tidewell Homecare</span></div>
  <nav class="main-nav">
    <span class="active">HOME</span><span>ABOUT US</span><span>SERVICES</span><span>PROJECTS</span><span>BLOG</span><span>CONTACT US</span>
  </nav>
</header>

<section class="hero" role="img" aria-label="Photo of a cleaner vacuuming a bright living room">
  <h1 class="hero-title">CLEANHOME SUCCESS IN EVERY PROJECTS</h1>
  <div class="hero-dots"><span class="on"></span><span class="on"></span><span></span></div>
</section>

<div class="service blue" style="left:0;width:390px">
  <div class="service-icon blue"><svg width="54" height="54" viewBox="0 0 54 54" fill="none" stroke="#fff" stroke-width="2.5"><rect x="12" y="6" width="30" height="42"/><path d="M18 14h6M30 14h6M18 22h6M30 22h6M18 30h6M30 30h6M23 48v-9h8v9M4 48h46"/></svg></div>
  <h3>Commercial Cleaning</h3>
  <p>Lorem ipsum dolor sit amet, consectetur adipiscing elit, sed do eiusmod tempor incididunt ut labore et dolore magna aliqua. Ut enim ad minim veniam.</p>
</div>
<div class="service yellow" style="left:404px;width:392px">
  <div class="service-icon yellow"><svg width="56" height="56" viewBox="0 0 56 56" fill="none" stroke="#222" stroke-width="2.5"><path d="M8 28L28 10l20 18M14 24v24h28V24M24 48V36h8v12"/><path d="M40 6l2 4 4 2-4 2-2 4-2-4-4-2 4-2z"/></svg></div>
  <h3>Home Cleaning</h3>
  <p>Lorem ipsum dolor sit amet, consectetur adipiscing elit, sed do eiusmod tempor incididunt ut labore et dolore magna aliqua. Ut enim ad minim veniam.</p>
</div>
<div class="service blue" style="left:810px;width:390px">
  <div class="service-icon blue"><svg width="54" height="54" viewBox="0 0 54 54" fill="none" stroke="#fff" stroke-width="2.5"><rect x="8" y="20" width="16" height="28" rx="4"/><path d="M12 20v-6h8v6"/><rect x="30" y="18" width="16" height="30" rx="2"/><path d="M34 18V8h10l4 6"/></svg></div>
  <h3>Maintenance</h3>
  <p>Lorem ipsum dolor sit amet, consectetur adipiscing elit, sed do eiusmod tempor incididunt ut labore et dolore magna aliqua. Ut enim ad minim veniam.</p>
</div>

<h2 class="section-title" style="top:955px">WELCOME TO TIDEWELL HOMECARE</h2>
<p class="welcome-text">Lorem ipsum dolor sit amet, consectetur adipiscing elit, sed do eiusmod tempor incididunt ut labore et dolore magna aliqua. Ut enim ad minim veniam, quis nostrud exercitation ullamco laboris nisi ut aliquip ex ea commodo consequat. Duis aute irure dolor in reprehenderit in voluptate velit esse cillum dolore eu fugiat nulla pariatur. Excepteur sint occaecat cupidatat non proident.</p>
<div class="btn btn-blue" style="left:522px;top:1169px;width:154px;height:45px">READ MORE</div>

<section class="clean-band">
  <svg class="clean-photo" width="600" height="511" role="img" aria-label="Photo of two cleaners wiping a table and mopping the floor">
    <defs><linearGradient id="cleanPhoto" x1="0" y1="0" x2="1" y2="1"><stop offset="0" stop-color="#e9e4da"/><stop offset="1" stop-color="#c9cfc6"/></linearGradient></defs>
    <polygon points="0,0 505,0 590,511 0,511" fill="url(#cleanPhoto)"/>
  </svg>
  <h2>OUR CLEANING SERVICES</h2>
  <p class="clean-sub">Sed ut perspiciatis unde omnis iste natus error sit voluptatem</p>
  <div class="tick-item" style="top:158px"><svg width="28" height="28" viewBox="0 0 28 28" fill="none" stroke="#fff" stroke-width="2"><circle cx="14" cy="14" r="12"/><path d="M8 14l5 5 9-10"/></svg><span>Lorem ipsum dolor sit amet, consectetur adipiscing elit, sed do eiusmod tempor incididunt ut labore</span></div>
  <div class="tick-item" style="top:242px"><svg width="28" height="28" viewBox="0 0 28 28" fill="none" stroke="#fff" stroke-width="2"><circle cx="14" cy="14" r="12"/><path d="M8 14l5 5 9-10"/></svg><span>Sed ut perspiciatis unde omnis iste natus error sit voluptatem accusantium doloremque .</span></div>
  <div class="tick-item" style="top:320px"><svg width="28" height="28" viewBox="0 0 28 28" fill="none" stroke="#fff" stroke-width="2"><circle cx="14" cy="14" r="12"/><path d="M8 14l5 5 9-10"/></svg><span>Lorem ipsum dolor sit amet, consectetur adipiscing elit, sed do eiusmod tempor incididunt ut labore</span></div>
  <div class="tick-item" style="top:410px"><svg width="28" height="28" viewBox="0 0 28 28" fill="none" stroke="#fff" stroke-width="2"><circle cx="14" cy="14" r="12"/><path d="M8 14l5 5 9-10"/></svg><span>At vero eos et accusamus et iusto odio dignissimos ducimus qui blanditiis praesentium voluptatum .</span></div>
</section>

<h2 class="section-title" style="top:1912px">WHY CHOOSE US</h2>
<p class="why-sub">The world's Latest at clean cleaning service company we can clean your residential space including homes.</p>

<div class="abs" style="left:473px;top:2087px;width:254px;height:254px;border-radius:50%;background:#ececec"></div>
<div class="abs" role="img" aria-label="Photo of a smiling cleaner giving a thumbs up in a kitchen" style="left:488px;top:2102px;width:224px;height:224px;border-radius:50%;border:2px solid var(--blue);background:linear-gradient(135deg,#e6e9ec,#c7d1d8)"></div>

<div class="feature left" style="left:80px;top:2101px"><h4>EXPERT EMPLOYEE</h4><p>Lorem ipsum dolor sit amet, consectetur adipiscing elit, sed do</p></div>
<div class="feature left" style="left:80px;top:2238px"><h4>LOW COSTING</h4><p>Lorem ipsum dolor sit amet, consectetur adipiscing elit, sed do</p></div>
<div class="feature" style="left:825px;top:2101px"><h4>SECURE SERVICES</h4><p>Lorem ipsum dolor sit amet, consectetur adipiscing elit, sed do</p></div>
<div class="feature" style="left:825px;top:2238px"><h4>ON TIME FINISHED</h4><p>Lorem ipsum dolor sit amet, consectetur adipiscing elit, sed do</p></div>

<div class="f-icon" style="left:396px;top:2102px"><span><svg width="26" height="26" viewBox="0 0 26 26" fill="none" stroke="#fff" stroke-width="2"><circle cx="13" cy="7" r="4"/><path d="M5 24c0-6 4-10 8-10s8 4 8 10"/></svg></span></div>
<div class="f-icon" style="left:396px;top:2249px"><span><svg width="26" height="26" viewBox="0 0 26 26" fill="none" stroke="#fff" stroke-width="2"><rect x="4" y="8" width="18" height="14" rx="2"/><path d="M9 8V5h8v3M13 12v6M10 15h6"/></svg></span></div>
<div class="f-icon" style="left:741px;top:2102px"><span><svg width="26" height="26" viewBox="0 0 26 26" fill="none" stroke="#fff" stroke-width="2"><path d="M13 3l8 3v7c0 5-4 8-8 10-4-2-8-5-8-10V6z"/><path d="M9 13l3 3 5-6"/></svg></span></div>
<div class="f-icon" style="left:741px;top:2249px"><span><svg width="26" height="26" viewBox="0 0 26 26" fill="none" stroke="#fff" stroke-width="2"><circle cx="13" cy="13" r="10"/><path d="M13 7v6l4 3"/></svg></span></div>

<section class="estimate" role="img" aria-label="Blue-tinted photo of a tidy living room">
  <h2>GET A FREE ESTIMATE TODAY</h2>
  <div class="field" style="left:109px;top:163px"><span>Name<em>*</em></span></div>
  <div class="field" style="left:356px;top:163px"><span>Email<em>*</em></span></div>
  <div class="field" style="left:608px;top:163px"><span>City<em>*</em></span></div>
  <div class="field" style="left:855px;top:163px"><span>Square Footage<em>*</em></span></div>
  <div class="field" style="left:109px;top:241px"><span>ProperType</span><svg width="14" height="9" viewBox="0 0 14 9" fill="none" stroke="#444" stroke-width="1.6"><path d="M1 1l6 6 6-6"/></svg></div>
  <div class="field" style="left:356px;top:241px"><span>Type Cleaning</span><svg width="14" height="9" viewBox="0 0 14 9" fill="none" stroke="#444" stroke-width="1.6"><path d="M1 1l6 6 6-6"/></svg></div>
  <div class="field" style="left:608px;top:241px"><span>Frequency</span><svg width="14" height="9" viewBox="0 0 14 9" fill="none" stroke="#444" stroke-width="1.6"><path d="M1 1l6 6 6-6"/></svg></div>
  <div class="field" style="left:855px;top:241px"><span>mm/dd/yyyy</span><svg width="26" height="26" viewBox="0 0 26 26" fill="none" stroke="#33a6d7" stroke-width="1.8"><rect x="2" y="4" width="22" height="20" rx="2"/><path d="M2 10h22M8 2v4M18 2v4M7 14h2M12 14h2M17 14h2M7 19h2M12 19h2M17 19h2"/></svg></div>
  <div class="btn btn-white" style="left:522px;top:345px;width:154px;height:45px">READ MORE</div>
</section>

<h2 class="section-title" style="top:2982px">LATEST FROM BLOG</h2>

<article class="blog-card" style="left:110px">
  <div class="blog-img" role="img" aria-label="Photo of a cleaning team tidying a living room"></div>
  <div class="date">11<small>A<br>P<br>R</small></div>
  <div class="author"><i></i>BY ADMIN</div>
  <p>At vero eos et accusamus et iusto odio dignissimos ducimus qui blanditiis praesentium .</p>
  <div class="btn btn-blue">READ MORE</div>
</article>
<article class="blog-card" style="left:448px">
  <div class="blog-img" role="img" aria-label="Photo of a cleaner scrubbing a bathroom"></div>
  <div class="date">11<small>A<br>P<br>R</small></div>
  <div class="author"><i></i>BY ADMIN</div>
  <p>At vero eos et accusamus et iusto odio dignissimos ducimus qui blanditiis praesentium .</p>
  <div class="btn btn-blue">READ MORE</div>
</article>
<article class="blog-card" style="left:783px">
  <div class="blog-img" role="img" aria-label="Photo of a cleaner vacuuming a bright room"></div>
  <div class="date">11<small>A<br>P<br>R</small></div>
  <div class="author"><i></i>BY ADMIN</div>
  <p>At vero eos et accusamus et iusto odio dignissimos ducimus qui blanditiis praesentium .</p>
  <div class="btn btn-blue">READ MORE</div>
</article>
<div class="pager"><span></span><span class="on"></span><span></span></div>

<footer class="site-footer">
  <h5 style="left:113px">ABOUT US</h5>
  <p class="f-about">Lorem ipsum dolor sit amet, consectetur adipiscing elit, sed do eiusmod tempor incididunt ut labore et dolore magna aliqua. Ut enim ad minim veniam,</p>
  <h5 style="left:461px">QUICKLINK</h5>
  <ul class="f-links"><li>HOME</li><li>ABOUT US</li><li>SERVICES</li><li>CASE STUDIES</li><li>BLOG</li><li>CONTACT US</li></ul>
  <h5 style="left:641px">CONTACT US</h5>
  <div class="f-contact">
    <p style="font-weight:700">555-014-2290</p>
    <p style="margin-top:16px">hello@tidewellhomecare.example</p>
    <p style="margin-top:24px">12 Harbour Lane, Brightwater,<br>CA 90210</p>
  </div>
  <h5 style="left:948px">FOLLOW US</h5>
  <div class="socials"><span></span><span></span><span></span></div>
  <p class="copyright">Copyrights © 2020 Copyrights Company Name | All Rights Reserved</p>
</footer>

</body>
</html>
```